New Business Card for Software Company

We are looking at rebranding a 10 year old company that specializes in PDF and DWF solutions for Architects and Engineers. We will attach the new company logo that we are going with so you can work with that and complimentary colors.
The sample information we would like on the business card is:
Gerald Pinfold
Vice President
4738 W. Harrowgate Lane. STE 305
PMB#417
Larkmont, CO 85374
866-392-5074 US Toll Free
123-456-3190 Cell
gpinfold@plavorix.com
The old tag line that we had on the business cars was.
Delivering Dependable Drawing and Document Tools to Design Teams Worldwide.
If you have an idea for a better tag line we are open to that also.
Updates
We would like to thank all of the Designers for their wonderful work. We apologize that we will not have the time to provide feedback to everyone. There is just so many innovative and professional designs that you have all created making our decision even harder.
Target Market(s)
Architects and Engineers
Industry/Entity Type
Business
Look and feel

```html
<!DOCTYPE html>
<html lang="en">
<head>
<meta charset="utf-8">
<title>Plavorix Business Card</title>
<link rel="stylesheet" href="https://fonts.googleapis.com/css2?family=Arimo:wght@400;700&family=Source+Sans+3:wght@400;600&display=swap">
<style>
  :root {
    --red: #c8242f;
    --red-deep: #b51c2a;
    --orange: #f07a1a;
    --orange-bright: #f7a21c;
    --amber: #ffb347;
    --ink: #58595b;
    --rule: #9a9a9a;
    --paper: #ffffff;
    --stage: #ece9e4;
  }
  * { box-sizing: border-box; margin: 0; padding: 0; }
  html, body { width: 1200px; height: 720px; overflow: hidden; }
  body {
    background: var(--stage);
    font-family: "Arimo", Arial, sans-serif;
    position: relative;
  }
  .card {
    position: absolute;
    width: 540px;
    height: 309px;
    border-radius: 3px;
    overflow: hidden;
    box-shadow: 0 6px 18px rgba(0,0,0,.18);
  }
  /* Front */
  .card--front {
    left: 40px; top: 205px;
    background: var(--paper);
  }
  .band {
    position: absolute; left: 0; right: 0;
    background: linear-gradient(90deg, var(--red-deep) 0%, var(--red) 35%, var(--orange) 75%, var(--orange-bright) 100%);
    color: #fff;
  }
  .band--top { top: 0; height: 44px; padding: 12px 0 0 34px; }
  .band--bottom {
    bottom: 0; height: 40px; padding: 11px 0 0 34px;
    font-size: 14px; letter-spacing: .2px; font-style: normal;
  }
  .holder__name { font-weight: 700; font-size: 18px; }
  .holder__title { font-size: 12px; }
  .rule {
    position: absolute; left: 0; right: 0; height: 2px; background: var(--rule);
  }
  .rule--top { top: 50px; }
  .rule--bottom { bottom: 46px; }
  .brand {
    position: absolute; left: 40px; top: 92px;
    display: flex; align-items: center; gap: 14px;
  }
  .brand__dot {
    width: 64px; height: 64px; border-radius: 50%;
    background: var(--orange);
  }
  .brand__name {
    font-weight: 700; font-size: 66px; color: var(--ink);
    letter-spacing: -1px; line-height: 1;
  }
  .contacts {
    position: absolute; left: 34px; right: 20px; top: 198px;
    display: flex; gap: 22px; list-style: none;
    font-size: 13px; color: var(--ink);
  }
  .contacts__item { display: flex; align-items: center; gap: 6px; white-space: nowrap; }
  .contacts__icon { width: 11px; height: 11px; fill: var(--orange); }
  /* Back */
  .card--back {
    left: 620px; top: 205px;
    background: radial-gradient(circle at 50% 45%, var(--amber) 0%, var(--orange) 22%, var(--red) 62%, var(--red-deep) 100%);
    color: #fff;
  }
  .back__brand {
    position: absolute; left: 0; right: 0; top: 62px;
    display: flex; flex-direction: column; align-items: center; gap: 12px;
  }
  .back__dot {
    width: 92px; height: 92px; border-radius: 50%;
    background: var(--orange-bright);
  }
  .back__name { font-weight: 700; font-size: 28px; color: #fff; letter-spacing: .5px; }
  .tagline {
    position: absolute; left: 0; right: 0; bottom: 34px;
    font-family: "Source Sans 3", "Myriad Pro", sans-serif;
    font-size: 17px; line-height: 1.25; text-align: center;
  }
</style>
</head>
<body>
  <section class="card card--front" aria-label="Business card front">
    <div class="band band--top">
      <span class="holder__name">Gerald Pinfold,</span>
      <span class="holder__title">Vice President</span>
    </div>
    <div class="rule rule--top"></div>

    <div class="brand">
      <span class="brand__dot"></span>
      <span class="brand__name">plavorix</span>
    </div>

    <ul class="contacts">
      <li class="contacts__item">
        <svg class="contacts__icon" viewBox="0 0 12 12"><path d="M2.5 0.5h2l1 3-1.5 1c.7 1.5 1.8 2.6 3.3 3.3l1-1.5 3 1v2c0 1-1 1.7-2 1.6C4.6 10.4 1.6 7.4 .9 2.5.8 1.5 1.5.5 2.5.5z"/></svg>
        866-392-5074(US) TF
      </li>
      <li class="contacts__item">
        <svg class="contacts__icon" viewBox="0 0 12 12"><rect x="3" y="0" width="6" height="12" rx="1.2"/></svg>
        123-456-3190
      </li>
      <li class="contacts__item">
        <svg class="contacts__icon" viewBox="0 0 12 12"><path d="M0 2h12v8H0z M0 2l6 4.5L12 2"/></svg>
        gpinfold@plavorix.com
      </li>
    </ul>

    <div class="rule rule--bottom"></div>
    <address class="band band--bottom">
      4738 W. Harrowgate Lane. STE 305, PMB#417, Larkmont, CO 85374
    </address>
  </section>

  <section class="card card--back" aria-label="Business card back">
    <div class="back__brand">
      <span class="back__dot"></span>
      <span class="back__name">plavorix</span>
    </div>
    <p class="tagline">Delivering Dependable Drawing and Document Tools<br>to Design Teams Worldwide</p>
  </section>
</body>
</html>
```